Brimsett Gardening Fresh New Website

We are looking to create a simple fresh website for our landscaping business. The website should appeal to a 'high end' audience. We deal with a lot of Embassies and affluent clients who have extremely large gardens that are meticulously maintained. The site is about communicating our excellent landscaping and customer service skills and encouraging new clients to reach out and engage us to take care of their gardens.

The website is basically going to be our business card, it will have almost no functionality other than two 'contact us' forms, one for smaller clients and one for more detailed projects.

The website will not have a lot of written content and will have to show photos of beautifully landscaped gardens.

The main logo in black will influence the site, however, we are open to all suggestions.

We are expecting to have the following pages:
Home Page
Services
About Us
Contact Us
Showcase (photo gallery of our work)

We need someone who can code it to wordpress and be available for minor changes over a number of days. They will be simple tweaks.

```html
<!DOCTYPE html>
<html lang="en">
<head>
<meta charset="utf-8">
<title>Brimsett Gardening</title>
<link href="https://fonts.googleapis.com/css2?family=Poppins:ital,wght@0,400;0,500;0,600;0,700;0,800;1,600&family=Cinzel:wght@500&display=swap" rel="stylesheet">
<style>
:root{
  --gold:#a8732a;
  --gold-dark:#8a5a1a;
  --yellow:#e8b630;
  --ink:#1c1c1c;
  --text:#3a3a3a;
  --muted:#666;
  --cream:#fdf1e2;
  --dark:#1d1d1b;
  --line:#d9d9d9;
  --white:#fff;
}
*{margin:0;padding:0;box-sizing:border-box}
html,body{width:1200px;height:4648px;overflow:hidden}
body{font-family:"Poppins",sans-serif;color:var(--text);background:var(--white);position:relative}
.abs{position:absolute}
.btn{position:absolute;display:flex;align-items:center;justify-content:center;background:var(--gold);color:#fff;font-size:11px;font-weight:600;border-radius:4px;text-transform:uppercase;letter-spacing:.2px}
.section-title{position:absolute;left:0;width:1200px;text-align:center;font-size:35px;font-weight:700;color:var(--ink)}
.section-title span{color:var(--gold-dark)}

/* hero */
.hero{position:absolute;left:0;top:0;width:1200px;height:680px;background:radial-gradient(ellipse at 75% 30%,#6a8f3c 0%,#3f6a24 35%,#25451a 70%,#17300f 100%)}
.hero-curve{position:absolute;left:0;top:600px}
.nav{position:absolute;left:0;top:0;width:1200px;height:106px;border-bottom:1px solid rgba(232,182,48,.7)}
.nav a{position:absolute;top:66px;color:#fff;font-size:14px;text-decoration:none;transform:translateY(-50%)}
.nav-contact{position:absolute;left:947px;top:57px;width:113px;height:37px;background:linear-gradient(#f3c53c,#d99f1c);color:#fff;font-size:11px;font-weight:500;display:flex;align-items:center;justify-content:center;border-radius:3px}
.brand-badge{position:absolute;border-radius:50%;display:flex;flex-direction:column;align-items:center;justify-content:center;font-family:"Poppins",sans-serif;color:var(--yellow);font-weight:500;text-align:center;line-height:1.2}
.brand-top{left:538px;top:14px;width:124px;height:124px;background:#1f3413;border:2px solid var(--yellow);font-size:11px;letter-spacing:1.5px}
.hero-title{position:absolute;left:141px;top:240px;font-size:46px;font-weight:800;line-height:54px;color:#fff;text-transform:uppercase}
.hero-title .accent{color:var(--yellow)}
.hero-text{position:absolute;left:141px;top:418px;width:540px;font-size:13px;line-height:23px;color:#fff}
.scroll-mouse{position:absolute;left:568px;top:598px;width:66px;height:66px;border-radius:50%;background:#fff;box-shadow:0 4px 14px rgba(0,0,0,.2)}

/* about */
.about-photo{position:absolute;left:148px;top:740px;width:475px;height:442px;background:radial-gradient(ellipse at 50% 55%,#b9bec4 0%,#d9dde0 45%,#f4f5f6 80%,#fff 100%)}
.about-title{position:absolute;left:668px;top:786px;font-size:22px;font-weight:600;color:var(--ink)}
.about-title span{color:var(--gold)}
.about-text{position:absolute;left:664px;top:830px;width:395px;font-size:12.3px;line-height:21.2px;color:#333}
.about-text p+p{margin-top:21px}

/* services */
.services-bg{position:absolute;left:0;top:1312px;width:1200px;height:660px;background:linear-gradient(180deg,#eef1ea 0%,#e6ece2 50%,#eef0ea 100%)}
.service-card{position:absolute;top:1505px;width:218px;height:256px;border-radius:10px;overflow:hidden;color:#fff;text-align:center}
.service-card .ph{position:absolute;inset:0}
.service-card .shade{position:absolute;inset:0;background:linear-gradient(180deg,rgba(0,0,0,0) 35%,rgba(0,0,0,.65) 100%)}
.service-card h3{position:absolute;left:0;right:0;top:138px;font-size:15px;font-weight:600}
.service-card p{position:absolute;left:25px;right:25px;top:164px;font-size:11px;line-height:18px}
.service-card a{position:absolute;left:0;right:0;top:208px;font-size:11px;font-weight:600;color:#fff;text-decoration:underline}

/* gallery */
.gallery-item{position:absolute;width:292px;height:292px;border-radius:14px}

/* testimonials */
.testi-card{position:absolute;top:3108px;width:292px;height:284px;background:#fff;border-radius:12px;box-shadow:0 6px 20px rgba(160,120,60,.08)}
.stars{position:absolute;left:27px;top:28px;color:var(--yellow);font-size:17px;letter-spacing:5px}
.review-badge{position:absolute;right:28px;top:30px;width:22px;height:22px;border-radius:50%;border:3px solid #4a86e8}
.testi-card p{position:absolute;left:28px;top:80px;width:245px;font-size:12.3px;line-height:21.2px;color:#333}
.testi-card h4{position:absolute;left:28px;top:238px;font-size:14px;font-weight:600;font-style:italic;color:var(--ink)}
.arrow{position:absolute;top:3222px;width:54px;height:54px;border-radius:50%;display:flex;align-items:center;justify-content:center}

/* contact */
.contact-wrap{position:absolute;left:141px;top:3633px;width:918px;height:428px;background:#fff;border-radius:18px;box-shadow:0 4px 30px rgba(0,0,0,.06)}
.contact-card{position:absolute;left:141px;top:3633px;width:334px;height:428px;border-radius:18px;background:linear-gradient(160deg,#2d3328 0%,#141612 60%,#1f2a18 100%);color:#fff}
.contact-card .eyebrow{position:absolute;left:35px;top:54px;font-size:12px;color:var(--gold);font-weight:500}
.contact-card h3{position:absolute;left:35px;top:78px;font-size:25px;font-weight:400;line-height:38px}
.c-row{position:absolute;left:35px;display:flex;align-items:center;gap:12px;font-size:12px;line-height:21px}
.c-ico{width:30px;height:30px;border-radius:50%;border:1.5px solid #fff;display:flex;align-items:center;justify-content:center;flex:none}
.form-title{position:absolute;left:515px;top:3664px;font-size:15px;font-weight:500;color:var(--ink)}
.field{position:absolute;height:38px;border:1px solid var(--line);border-radius:2px;font-size:11px;color:#555;padding:11px 16px}

/* footer */
.footer{position:absolute;left:0;top:4224px;width:1200px;height:424px;background:linear-gradient(180deg,#22221f 0%,#1a1a18 100%)}
.brand-foot{left:515px;top:4192px;width:172px;height:172px;background:#1b1b19;border:3px solid var(--yellow);font-size:15px;letter-spacing:2px}
.foot-nav{position:absolute;left:0;top:4418px;width:1200px;display:flex;justify-content:center;gap:24px;font-size:13.5px;color:#fff}
.foot-line{position:absolute;left:141px;width:918px;height:1px;background:#55554f}
.foot-info{position:absolute;top:4503px;display:flex;gap:12px;align-items:center;font-size:12px;line-height:20px;color:#fff}
.copyright{position:absolute;left:0;top:4587px;width:1200px;text-align:center;font-size:12px;color:#fff}
</style>
</head>
<body>

<!-- Hero -->
<div class="hero" role="img" aria-label="Photo of a manicured garden lawn with flowering hedges and trees"></div>
<svg class="hero-curve" width="1200" height="80" viewBox="0 0 1200 80"><path d="M0 72 Q600 -20 1200 72 L1200 80 L0 80 Z" fill="#fff"/></svg>
<nav class="nav">
  <a style="left:140px">Home</a>
  <a style="left:262px">About Us</a>
  <a style="left:409px">Services</a>
  <a style="left:726px">Our Gallery</a>
  <div class="nav-contact">CONTACT US</div>
</nav>
<div class="brand-badge brand-top">BRIMSETT<br>GARDENING</div>
<h1 class="hero-title"><span class="accent">Brimsett Gardening</span><br>Your Full Landscaping<br>&amp; Lawn Care Experts</h1>
<p class="hero-text">Lorem ipsum dolor sit amet, consectetur adipiscing elit, sed do eiusmod tempor incididunt ut labore et dolore magna aliqua.</p>
<div class="btn" style="left:141px;top:486px;width:112px;height:38px">Read More</div>
<div class="scroll-mouse">
  <svg width="66" height="66" viewBox="0 0 66 66"><rect x="25" y="19" width="16" height="28" rx="8" fill="none" stroke="#111" stroke-width="2"/><line x1="33" y1="25" x2="33" y2="31" stroke="#111" stroke-width="2"/></svg>
</div>

<!-- About -->
<div class="about-photo" role="img" aria-label="Photo of a large white country house with a porch"></div>
<h2 class="about-title">About <span>Us</span></h2>
<div class="about-text">
  <p>Lorem ipsum dolor sit amet, consectetur adipiscing elit, sed do eiusmod tempor incididunt ut labore et dolore magna aliqua. Quis ipsum suspendisse ultrices gravida. Risus commodo viverra maecenas accumsan lacus vel facilisis. Lorem ipsum dolor sit amet, consectetur adipiscing elit, sed do eiusmod tempor incididunt ut labore et dolore magna aliqua. Quis ipsum suspendisse ultrices gravida. Risus commodo viverra maecenas accumsan lacus vel facilisis.</p>
  <p>Lorem ipsum dolor sit amet, consectetur adipiscing elit, sed do eiusmod tempor incididunt ut labore et dolore magna aliqua. Quis ipsum suspendisse ultrices gravida. Risus commodo viverra maecenas accumsan lacus vel facilisis.</p>
</div>
<div class="btn" style="left:664px;top:1130px;width:113px;height:38px">Read More</div>

<!-- Services -->
<div class="services-bg" role="img" aria-label="Faded photo of a park with trees and a lake"></div>
<svg class="abs" style="left:0;top:1920px" width="1200" height="60" viewBox="0 0 1200 60"><path d="M0 48 Q600 -8 1200 48 L1200 60 L0 60 Z" fill="#fff"/></svg>
<h2 class="section-title" style="top:1416px">Our <span>Services</span></h2>

<div class="service-card" style="left:141px">
  <div class="ph" role="img" aria-label="Photo of a single tree in a landscaped field" style="background:linear-gradient(180deg,#4d6a78 0%,#3f5a35 55%,#26381c 100%)"></div>
  <div class="shade"></div>
  <h3>Landscaping</h3><p>Lorem ipsum dolor sit amet, consectetur adipiscing.</p><a>Read More</a>
</div>
<div class="service-card" style="left:374px">
  <div class="ph" role="img" aria-label="Photo of hands using garden shears" style="background:linear-gradient(160deg,#a84a26 0%,#4e6a2c 50%,#2b3d1b 100%)"></div>
  <div class="shade"></div>
  <h3>Lawn Service</h3><p>Lorem ipsum dolor sit amet, consectetur adipiscing.</p><a>Read More</a>
</div>
<div class="service-card" style="left:608px">
  <div class="ph" role="img" aria-label="Photo of a wheelbarrow full of grass clippings" style="background:linear-gradient(160deg,#6d7a4a 0%,#4c5a38 50%,#2a3448 100%)"></div>
  <div class="shade"></div>
  <h3>Lawn Maintenance</h3><p>Lorem ipsum dolor sit amet, consectetur adipiscing.</p><a>Read More</a>
</div>
<div class="service-card" style="left:841px">
  <div class="ph" role="img" aria-label="Photo of workers clearing trees in a forest" style="background:linear-gradient(160deg,#5a4030 0%,#8a5030 40%,#3b3326 100%)"></div>
  <div class="shade"></div>
  <h3>Tree Services</h3><p>Lorem ipsum dolor sit amet, consectetur adipiscing.</p><a>Read More</a>
</div>
<div class="btn" style="left:518px;top:1811px;width:164px;height:39px">View All Services</div>

<!-- Gallery -->
<h2 class="section-title" style="top:2040px">Our <span>Gallery</span></h2>
<div class="gallery-item" style="left:141px;top:2140px;background:linear-gradient(160deg,#7ea23a,#3a6a25 60%,#2c3a2a)" role="img" aria-label="Photo of a wooden boardwalk through a lush garden"></div>
<div class="gallery-item" style="left:454px;top:2140px;background:linear-gradient(180deg,#5a7a2a,#8aa048 50%,#6e7a6a)" role="img" aria-label="Photo of a path under green garden arches"></div>
<div class="gallery-item" style="left:766px;top:2140px;background:linear-gradient(180deg,#2a88e0 0%,#6ab0ea 35%,#4a9a30 55%,#c83a2a 65%,#7ac43a 80%)" role="img" aria-label="Photo of a bright lawn with red flower beds under blue sky"></div>
<div class="gallery-item" style="left:141px;top:2451px;background:linear-gradient(180deg,#c8b8a8 0%,#a07a4a 40%,#8aa83a 70%,#c8a840)" role="img" aria-label="Photo of a park with benches and white fences in autumn"></div>
<div class="gallery-item" style="left:454px;top:2451px;background:linear-gradient(160deg,#2a5a2a,#a8c0b8 40%,#4a8a30 70%,#a09070)" role="img" aria-label="Photo of stone steps leading past a waterfall"></div>
<div class="gallery-item" style="left:766px;top:2451px;background:linear-gradient(180deg,#4a6a3a,#8a8a80 45%,#5a8a3a 80%,#3a6a2a)" role="img" aria-label="Photo of a stone gazebo with trimmed hedges"></div>
<div class="btn" style="left:525px;top:2792px;width:150px;height:39px">View All Gallery</div>

<!-- Testimonials -->
<svg class="abs" style="left:0;top:2894px" width="1200" height="640" viewBox="0 0 1200 640"><path d="M0 12 Q600 44 1200 12 L1200 618 Q600 560 0 618 Z" fill="#fdf1e2"/></svg>
<h2 class="section-title" style="top:3012px">Client <span>Testimonials</span></h2>

<div class="testi-card" style="left:141px"><div class="stars">★★★★★</div><div class="review-badge"></div><p>Lorem ipsum dolor sit amet, consectetur adipiscing elit, sed do eiusmod tempor incididunt ut labore et dolore magna aliqua. Quis ipsum suspendisse ultrices gravida. Risus commodo viverra maecenas accumsan lacus vel facilisis.</p><h4>Marla Denholm</h4></div>
<div class="testi-card" style="left:454px"><div class="stars">★★★★★</div><div class="review-badge"></div><p>Lorem ipsum dolor sit amet, consectetur adipiscing elit, sed do eiusmod tempor incididunt ut labore et dolore magna aliqua. Quis ipsum suspendisse ultrices gravida. Risus commodo viverra maecenas accumsan lacus vel facilisis.</p><h4>Marla Denholm</h4></div>
<div class="testi-card" style="left:766px"><div class="stars">★★★★★</div><div class="review-badge"></div><p>Lorem ipsum dolor sit amet, consectetur adipiscing elit, sed do eiusmod tempor incididunt ut labore et dolore magna aliqua. Quis ipsum suspendisse ultrices gravida. Risus commodo viverra maecenas accumsan lacus vel facilisis.</p><h4>Marla Denholm</h4></div>

<div class="arrow" style="left:64px;border:2px solid var(--gold)">
  <svg width="20" height="20" viewBox="0 0 20 20"><path d="M13 3 L6 10 L13 17" fill="none" stroke="#a8732a" stroke-width="2.4" stroke-linecap="round"/></svg>
</div>
<div class="arrow" style="left:1080px;background:var(--gold)">
  <svg width="20" height="20" viewBox="0 0 20 20"><path d="M7 3 L14 10 L7 17" fill="none" stroke="#fff" stroke-width="2.4" stroke-linecap="round"/></svg>
</div>

<!-- Contact -->
<div class="contact-wrap"></div>
<div class="contact-card" role="img" aria-label="Dark photo of a garden at dusk behind the contact details">
  <div class="eyebrow">CONTACT US</div>
  <h3>Ask One Of Our<br>Experts For Help</h3>
  <div class="c-row" style="top:183px"><span class="c-ico"><svg width="14" height="14" viewBox="0 0 24 24"><path d="M5 3h4l2 5-2.5 1.5a11 11 0 0 0 6 6L16 13l5 2v4a2 2 0 0 1-2 2A17 17 0 0 1 3 5a2 2 0 0 1 2-2z" fill="none" stroke="#fff" stroke-width="2"/></svg></span>+91 123-456-7890</div>
  <div class="c-row" style="top:236px"><span class="c-ico"><svg width="14" height="14" viewBox="0 0 24 24"><rect x="3" y="6" width="18" height="12" fill="none" stroke="#fff" stroke-width="2"/><path d="M3 6l9 7 9-7" fill="none" stroke="#fff" stroke-width="2"/></svg></span>hello@brimsettgardens.example</div>
  <div class="c-row" style="top:282px"><span class="c-ico"><svg width="14" height="14" viewBox="0 0 24 24"><path d="M12 22s7-7 7-12a7 7 0 0 0-14 0c0 5 7 12 7 12z" fill="none" stroke="#fff" stroke-width="2"/><circle cx="12" cy="10" r="2.5" fill="#fff"/></svg></span>Lorem Ipsum is simply of the<br>printing and typesetting industry.</div>
</div>
<div class="form-title">DROP YOUR MESSAGE</div>
<div class="field" style="left:515px;top:3720px;width:247px;border-color:#c9a56a">First Name</div>
<div class="field" style="left:772px;top:3720px;width:248px">Last Name</div>
<div class="field" style="left:515px;top:3768px;width:247px">Email Address</div>
<div class="field" style="left:772px;top:3768px;width:248px">Phone</div>
<div class="field" style="left:515px;top:3818px;width:505px;height:138px">Message</div>
<div class="btn" style="left:515px;top:3985px;width:128px;height:38px">Submit Now</div>

<!-- Footer -->
<svg class="abs" style="left:0;top:4210px" width="1200" height="40" viewBox="0 0 1200 40"><path d="M0 14 Q600 -4 1200 14 L1200 40 L0 40 Z" fill="#22221f"/></svg>
<div class="footer" role="img" aria-label="Dark faded photo of a garden"></div>
<div class="brand-badge brand-foot">BRIMSETT<br>GARDENING</div>
<div class="foot-nav"><span>Home</span><span>About Us</span><span>Services</span><span>Our Gallery</span><span>Contact Us</span></div>
<div class="foot-line" style="top:4477px"></div>
<div class="foot-info" style="left:141px"><svg width="20" height="20" viewBox="0 0 24 24"><circle cx="12" cy="12" r="9" fill="none" stroke="#fff" stroke-width="1.6"/><path d="M3 12h18M12 3a14 14 0 0 1 0 18M12 3a14 14 0 0 0 0 18" fill="none" stroke="#fff" stroke-width="1.4"/></svg><span>Lorem Ipsum is simply dummy text<br>of the printing and typesetting.</span></div>
<div class="foot-info" style="left:506px"><svg width="20" height="20" viewBox="0 0 24 24"><path d="M5 3h4l2 5-2.5 1.5a11 11 0 0 0 6 6L16 13l5 2v4a2 2 0 0 1-2 2A17 17 0 0 1 3 5a2 2 0 0 1 2-2z" fill="none" stroke="#fff" stroke-width="1.6"/></svg><span>Call Us<br>123-456-7890</span></div>
<div class="foot-info" style="left:797px"><svg width="20" height="20" viewBox="0 0 24 24"><rect x="3" y="6" width="18" height="13" fill="none" stroke="#fff" stroke-width="1.6"/><path d="M3 6l9 7 9-7" fill="none" stroke="#fff" stroke-width="1.6"/></svg><span>Email<br>hello@brimsettgardens.example</span></div>
<div class="foot-line" style="top:4561px"></div>
<div class="copyright">© 2024 Brimsett Landscaping Gardening. All Rights Reserved.</div>

</body>
</html>
```